NZ First of it's kind solutions directory and marketplace for busy Mums needs a business card design

We need a business card design for our new nationwide business in NZ (long term plans to go global). We provide solutions to the everyday challenges that busy Mums face by connecting them with quality communities and suppliers of carefully selected, relevant products and services. We sell direct via our online marketplace. The final design should communicate our values of inclusivity, quality and smart solutions. Colours should incorporate our logo colour palette of #477077 and #6ba8b2. Our website is at https://www.brightnestmums.example

Target Market(s)

busy Mums, Age 28 – 50, female, income over $100K, location main centres NZ primarily but NZ wide. Is likely juggling work or career with a young family. Probably had hobbies which have fallen by the wayside.
-Wants to succeed in her chosen career without compromising on family life
-to successfully juggle her career without feeling like she is compromising her children
- Is time poor, something always has to give and it’s generally her health (she’ll stay up late, get stressed)
- probably ex corporate or professional career. Has discretional income

Industry/Entity Type

Business

Contact Information for Business Card

Lena Forbisher, Founder, BrightNestMums.example (Strapline Tap; Gather; Sorted), 47 Kowhai Terrace, Ellerslie, Auckland 1051, New Zealand. Mob: 021 483 517 Ph: +64 (0)9 571 4860

Font styles to use
Other font styles liked:
• Raleway, and/or Architects Daughter

Colors
00a990
33b8a4
86cfc6
cfeae6

Requirements
Must have
• the above details, streamline. the logo and colours associated with those logos
Should not have
• foil or metallic colours

```html
<!DOCTYPE html>
<html lang="en">
<head>
<meta charset="utf-8">
<title>BrightNestMums business card</title>
<link rel="stylesheet" href="https://fonts.googleapis.com/css2?family=Arimo:wght@400;700&display=swap">
<style>
  :root {
    --teal-deep: #477077;
    --teal-light: #6ba8b2;
    --card-back: #4a7078;
    --card-front: #ffffff;
    --ink: #3a3a3a;
    --ink-strong: #4d4d4d;
    --stage: #ecebe8;
  }
  * { box-sizing: border-box; margin: 0; padding: 0; }
  html, body {
    width: 1200px; height: 900px; overflow: hidden;
    background: var(--stage);
    font-family: "Arimo", Arial, sans-serif;
  }
  .canvas {
    width: 1200px; height: 900px;
    display: flex; flex-direction: column;
    align-items: center; justify-content: center; gap: 60px;
  }
  .card {
    width: 630px; height: 360px; position: relative;
    box-shadow: 0 6px 18px rgba(0,0,0,0.18);
  }
  /* back side */
  .card-back {
    background: var(--card-back);
    display: flex; align-items: center; justify-content: center;
  }
  .card-back .wordmark {
    color: #ffffff; font-size: 44px; font-weight: 700; letter-spacing: -0.5px;
  }
  /* front side */
  .card-front { background: var(--card-front); }
  .brand {
    position: absolute; left: 44px; top: 92px;
    display: flex; align-items: center; gap: 16px;
  }
  .brand-dot {
    width: 46px; height: 46px; border-radius: 50%;
    background: var(--teal-deep);
  }
  .brand .wordmark {
    color: var(--teal-deep); font-size: 42px; font-weight: 700; letter-spacing: -0.5px;
  }
  .person { position: absolute; left: 44px; top: 210px; }
  .person-name { font-size: 22px; font-weight: 700; color: var(--ink-strong); letter-spacing: 0.3px; }
  .person-name .given { color: var(--teal-deep); }
  .person-role { font-size: 16px; color: var(--ink); margin-top: 2px; }
  .contacts {
    position: absolute; left: 44px; top: 270px;
    list-style: none; font-size: 17px; color: var(--ink); line-height: 24px;
  }
  .contacts li { display: flex; align-items: center; gap: 8px; }
  .contacts svg { width: 13px; height: 13px; fill: var(--ink); flex: none; }
  .address {
    position: absolute; right: 36px; top: 214px;
    font-size: 14px; line-height: 20px; color: var(--ink); text-align: right;
    font-style: normal;
  }
</style>
</head>
<body>
<main class="canvas">
  <section class="card card-back" aria-label="Card back">
    <span class="wordmark">BrightNestMums</span>
  </section>

  <section class="card card-front" aria-label="Card front">
    <div class="brand">
      <span class="brand-dot"></span>
      <span class="wordmark">BrightNestMums</span>
    </div>

    <div class="person">
      <p class="person-name"><span class="given">LENA</span> FORBISHER</p>
      <p class="person-role">Founder</p>
    </div>

    <ul class="contacts">
      <li>
        <svg viewBox="0 0 16 16" aria-hidden="true"><path d="M2 5c0-2 2-3 6-3s6 1 6 3v1h-3V5H5v1H2zM3 8l2-2h6l2 2v6H3zm5 1a2 2 0 1 0 0 4 2 2 0 0 0 0-4z"/></svg>
        021 483 517
      </li>
      <li>
        <svg viewBox="0 0 16 16" aria-hidden="true"><path d="M4 1h8a1 1 0 0 1 1 1v12a1 1 0 0 1-1 1H4a1 1 0 0 1-1-1V2a1 1 0 0 1 1-1zm1 2v8h6V3zm3 9a1 1 0 1 0 0 2 1 1 0 0 0 0-2z"/></svg>
        +64 (0)9 571 4860
      </li>
      <li>
        <svg viewBox="0 0 16 16" aria-hidden="true"><circle cx="8" cy="8" r="7"/></svg>
        www.BrightNestMums.example
      </li>
    </ul>

    <address class="address">
      47 Kowhai Terrace, Ellerslie<br>
      Auckland 1051, New Zealand
    </address>
  </section>
</main>
</body>
</html>
```